RTavenor Business Cards & Letterhead

I have a logo but need a design for some new business cards. We are a Design-Build Firm that specializes in the design and construction of commercial projects.
the cards need to be professional. no cartoon stuff.
i would like to have the cards in AI format so I can update the card as needed. Logo is provided.
Our Address is: 4187 Marlowe Ct. Elmfield, South Dakota 27614

```html
<!DOCTYPE html>
<html lang="en">
<head>
<meta charset="utf-8">
<title>RTavenor Business Card</title>
<link href="https://fonts.googleapis.com/css2?family=Open+Sans:wght@400;600;700;800&display=swap" rel="stylesheet">
<style>
  :root {
    --stage: #333335;
    --card: #1f1f23;
    --logo-grey: #707176;
    --brand-blue: #1a78c2;
    --band-dark: #0a3a62;
    --band-light: #1479bf;
    --rule-grey: #7a7b80;
    --white: #ffffff;
  }
  html, body {
    margin: 0;
    width: 1200px;
    height: 780px;
    overflow: hidden;
    background: var(--stage);
    font-family: "Open Sans", Arial, sans-serif;
  }
  .card {
    position: absolute;
    top: 230px;
    width: 560px;
    height: 320px;
    background: var(--card);
    overflow: hidden;
    box-shadow: 0 10px 28px rgba(0,0,0,0.45);
  }
  .card--back { left: 20px; }
  .card--front { left: 620px; }

  .wordmark {
    position: absolute;
    display: flex;
    align-items: center;
    gap: 12px;
    color: var(--logo-grey);
    font-weight: 800;
    letter-spacing: 1px;
  }
  .wordmark__square { background: var(--brand-blue); }
  .card--back .wordmark {
    left: 0; right: 0; top: 0; bottom: 0;
    justify-content: center;
    font-size: 58px;
  }
  .card--back .wordmark__square { width: 44px; height: 44px; }
  .card--front .wordmark {
    left: 150px;
    top: 48px;
    font-size: 44px;
  }
  .card--front .wordmark__square { width: 32px; height: 32px; }

  .identity {
    position: absolute;
    left: 38px;
    top: 162px;
    text-align: right;
  }
  .identity__name {
    color: var(--brand-blue);
    font-size: 24px;
    font-weight: 700;
    letter-spacing: 1px;
    line-height: 1.1;
  }
  .identity__title {
    color: var(--white);
    font-size: 15px;
    font-weight: 600;
    letter-spacing: 0.5px;
  }
  .divider {
    position: absolute;
    left: 300px;
    top: 144px;
    width: 2px;
    height: 76px;
    background: var(--white);
  }
  .contacts {
    position: absolute;
    left: 316px;
    top: 146px;
    margin: 0;
    padding: 0;
    list-style: none;
  }
  .contacts__item {
    display: flex;
    align-items: center;
    gap: 8px;
    color: var(--white);
    font-size: 14px;
    line-height: 23px;
    letter-spacing: 0.3px;
  }
  .contacts__icon { width: 13px; height: 13px; flex: none; }

  .band { position: absolute; left: 0; top: 0; }
  .address {
    position: absolute;
    left: 0; right: 0;
    bottom: 22px;
    text-align: center;
    color: var(--white);
    font-size: 17px;
    font-weight: 600;
    letter-spacing: 0.6px;
  }
</style>
</head>
<body>

<section class="card card--back" aria-label="Business card back">
  <div class="wordmark">
    <span class="wordmark__square"></span>
    <span class="wordmark__name">RTAVENOR</span>
  </div>
</section>

<section class="card card--front" aria-label="Business card front">
  <svg class="band" width="560" height="320" viewBox="0 0 560 320" aria-hidden="true">
    <defs>
      <linearGradient id="bandFill" x1="0" y1="0" x2="1" y2="0">
        <stop offset="0" stop-color="var(--band-dark)"/>
        <stop offset="0.62" stop-color="var(--band-light)"/>
        <stop offset="1" stop-color="var(--band-dark)"/>
      </linearGradient>
    </defs>
    <path d="M0 262 Q300 256 560 176 L560 320 L0 320 Z" fill="url(#bandFill)"/>
    <path d="M40 254 Q320 242 545 164" fill="none" stroke="var(--rule-grey)" stroke-width="3" stroke-linecap="round"/>
  </svg>

  <div class="wordmark">
    <span class="wordmark__square"></span>
    <span class="wordmark__name">RTAVENOR</span>
  </div>

  <div class="identity">
    <div class="identity__name">MARCUS TAVENOR</div>
    <div class="identity__title">Founder/President</div>
  </div>

  <div class="divider"></div>

  <ul class="contacts">
    <li class="contacts__item">
      <svg class="contacts__icon" viewBox="0 0 16 16" aria-hidden="true"><path d="M3 1l3 3-1.5 2a9 9 0 0 0 5.5 5.5L12 10l3 3-2 2C7 15 1 9 1 3z" fill="var(--brand-blue)"/></svg>
      (463) 555-0148
    </li>
    <li class="contacts__item">
      <svg class="contacts__icon" viewBox="0 0 16 16" aria-hidden="true"><circle cx="8" cy="8" r="6.5" fill="none" stroke="var(--brand-blue)" stroke-width="1.6"/><ellipse cx="8" cy="8" rx="2.8" ry="6.5" fill="none" stroke="var(--brand-blue)" stroke-width="1.3"/><path d="M1.5 8h13" stroke="var(--brand-blue)" stroke-width="1.3"/></svg>
      www.rtavenor.com
    </li>
    <li class="contacts__item">
      <svg class="contacts__icon" viewBox="0 0 16 16" aria-hidden="true"><rect x="1" y="3" width="14" height="10" rx="1" fill="var(--brand-blue)"/><path d="M1.5 3.5L8 9l6.5-5.5" fill="none" stroke="var(--card)" stroke-width="1.3"/></svg>
      MRT@RTavenor.com
    </li>
  </ul>

  <div class="address">4187 Marlowe Ct. Elmfield, South Dakota 27614</div>
</section>

</body>
</html>
```